The Visual Personality of Miss Cobbler Food Trailer

Something that stands out with color and our logo. This is a food trailer that attends several events in the spring and summer. We are known for being one of the best Gumbo producers in mid Michigan. We have been responsible for connecting different communities and cultures together and we are strong supporters of our veterans since this is a veteran owned business. All of our vegetables are fresh and locally purchased. These recipes are originally from New Orleans Louisiana. Our website is Misscobbler.net. This will be used for an 8" x 11" poster. Leave a box or area that states "WHERE WE WILL BE:" so that we can add the location of the event that we are attending.

Target Market(s)

We do cuisine that is recognized in the southern states of the USA. but live in the northern part of the USA. We are providing a menu of different southern recipes so they do not have to go all the way down south for get..

Industry/Entity Type

Food/Restaurant Industry

Font styles to use
Serif
Decorative

Colors
0094D4
00A9DD
6FCCEA
C7EBF8
E9F6FB
59FF00
82FF00
B8FF75
E3FFCB
F4FFEA
FFF300
FFF600
FEFA6F
FFFEC7
FFFEE8
EE7325
F08F49
F5BC92
FAE3D3
FDF4ED
EB3D1F
EC4F4E
F09395
F8D3D4
FCEDEE
A7469A
B969AE
D3A5CF
EDDBEB
F8F0F9

Requirements
Must have
• Our logo, which is "Miss Cobbler", "Homemade Deliciousness". We need an area on the poster where we can manually add the location of the event we will be attending because it changes weekly. location
Nice to have
• Bold colors and logo

```html
<!DOCTYPE html>
<html lang="en">
<head>
<meta charset="utf-8">
<title>Miss Cobbler Food Trailer – Poster</title>
<link rel="stylesheet" href="https://fonts.googleapis.com/css2?family=Fraunces:opsz,wght@9..144,600;9..144,800;9..144,900&family=Jost:ital,wght@0,400;0,500;0,700;1,500&family=Poppins:ital,wght@0,600;1,500&display=swap">
<style>
  :root {
    --bg: #e4e4e4;
    --red-bright: #b8161d;
    --red-mid: #96161f;
    --red-deep: #5e1520;
    --cream: #f2efe8;
    --gold: #e6de9a;
    --ink: #2a2225;
    --paper: #f4f3f1;
  }
  * { box-sizing: border-box; margin: 0; padding: 0; }
  html, body { width: 1200px; height: 1200px; overflow: hidden; background: var(--bg); }
  .canvas { position: relative; width: 1200px; height: 1200px; }
  .poster {
    position: absolute; left: 171px; top: 40px;
    width: 913px; height: 1191px;
    transform: scale(0.94); transform-origin: 0 0;
    overflow: hidden;
    background:
      radial-gradient(ellipse 70% 50% at 25% 8%, var(--red-bright), transparent 70%),
      linear-gradient(175deg, var(--red-bright) 0%, var(--red-mid) 40%, var(--red-deep) 100%);
    box-shadow: 0 10px 30px rgba(0,0,0,.18);
  }
  .brand-tab {
    position: absolute; left: 123px; top: 0; width: 240px; height: 249px;
    background: var(--paper);
    clip-path: polygon(0 0, 100% 0, 100% 92%, 96% 100%, 4% 100%, 0 92%);
    display: flex; flex-direction: column; align-items: center; justify-content: center; gap: 14px;
  }
  .brand-mark { width: 22px; height: 22px; border-radius: 50%; background: var(--red-bright); }
  .brand-name {
    font-family: 'Fraunces', serif; font-weight: 800; font-size: 30px;
    color: var(--ink); text-align: center; line-height: 1.05;
  }
  .footer-wave { position: absolute; left: 0; top: 0; width: 913px; height: 1191px; }
  .food { position: absolute; }
  .food-pizza {
    left: 500px; top: -30px; width: 560px; height: 390px;
    border-radius: 48% 52% 40% 60% / 50% 50% 50% 50%;
    background:
      radial-gradient(ellipse 60% 55% at 60% 40%, #d96a4a 0%, #e3a070 30%, transparent 62%),
      radial-gradient(ellipse at 45% 55%, #efe4ae 0%, #e6d693 60%, #cdb56c 100%);
    box-shadow: 0 8px 20px rgba(0,0,0,.25);
  }
  .food-gumbo {
    left: 490px; top: 340px; width: 490px; height: 460px; border-radius: 50%;
    background: radial-gradient(ellipse 50% 50% at 50% 50%,
      #c9784d 0%, #b9613c 35%, #9d4b2f 68%, #8a7a55 76%, #f3f0ea 78%, #e3ded4 96%, #cfc8bc 100%);
    box-shadow: 0 10px 24px rgba(0,0,0,.3);
  }
  .food-poboy {
    left: 440px; top: 752px; width: 500px; height: 440px;
    border-radius: 40% 20% 30% 34% / 26% 20% 40% 44%;
    background: linear-gradient(180deg,
      #c98e58 0%, #dba976 20%, #b77a47 30%, #e6ecd2 36%, #d5573f 46%,
      #e4b3a0 56%, #c78650 70%, #b5733f 88%, #a7683a 100%);
    box-shadow: 0 10px 24px rgba(0,0,0,.3);
  }
  .dish-label {
    position: absolute; font-family: 'Fraunces', serif; font-weight: 900;
    font-size: 31px; line-height: 1.0; color: var(--ink); text-align: center;
    text-shadow: 2px 0 0 #fff, -2px 0 0 #fff, 0 2px 0 #fff, 0 -2px 0 #fff,
                 2px 2px 0 #fff, -2px -2px 0 #fff, 2px -2px 0 #fff, -2px 2px 0 #fff;
  }
  .label-pizza { left: 712px; top: 158px; }
  .label-gumbo { left: 696px; top: 552px; }
  .label-poboy { left: 700px; top: 960px; }
  .message { position: absolute; left: 75px; top: 305px; width: 336px; color: var(--cream); text-align: center; }
  .tagline { font-family: 'Fraunces', serif; font-weight: 800; font-size: 47px; line-height: 0.98; letter-spacing: -0.5px; }
  .pitch { font-family: 'Jost', sans-serif; margin-top: 36px; }
  .pitch .xl { display: block; font-size: 68px; font-weight: 500; line-height: 0.95; letter-spacing: -0.5px; }
  .pitch .accent { color: var(--gold); font-weight: 700; }
  .pitch .sm { display: block; font-size: 30px; font-weight: 400; line-height: 1.2; }
  .pitch .md { display: block; font-size: 35px; font-weight: 400; line-height: 1.15; }
  .pitch .big { display: block; font-size: 60px; font-weight: 700; line-height: 1.05; color: var(--gold); padding-bottom: 12px; }
  .pitch .from { display: flex; align-items: center; gap: 12px; font-size: 30px; line-height: 1.1; }
  .pitch .from::before, .pitch .from::after { content: ""; flex: 1; height: 2px; background: var(--cream); }
  .location-label {
    position: absolute; left: 75px; top: 930px; width: 336px; text-align: center;
    font-family: 'Jost', sans-serif; font-style: italic; font-weight: 500; font-size: 16px;
    color: var(--cream); letter-spacing: .3px;
  }
  .location-box {
    position: absolute; left: 75px; top: 960px; width: 336px; height: 48px;
    border-radius: 24px; background: linear-gradient(180deg, #ffffff, #e9e9e9);
  }
  .footer { position: absolute; font-family: 'Poppins', sans-serif; color: var(--ink); }
  .footer .head { font-style: italic; font-weight: 500; font-size: 14px; }
  .footer .line { font-weight: 600; font-size: 15px; display: flex; align-items: center; gap: 12px; }
  .info { right: 651px; top: 1072px; text-align: right; }
  .info .head { margin-bottom: 10px; }
  .info .line { justify-content: flex-end; margin-bottom: 8px; }
  .icon-box { width: 20px; height: 20px; background: var(--red-mid); display: inline-flex; align-items: center; justify-content: center; }
  .divider { position: absolute; left: 281px; top: 1074px; width: 2px; height: 82px; background: var(--ink); }
  .social { left: 298px; top: 1072px; }
  .social .squares { display: flex; gap: 8px; margin: 8px 0 6px; }
  .social .sq { width: 30px; height: 30px; border: 2px solid var(--red-mid); border-radius: 6px; }
</style>
</head>
<body>
<div class="canvas">
  <div class="poster">
    <svg class="footer-wave" viewBox="0 0 913 1191" aria-hidden="true">
      <path d="M0,1191 L0,1098 C70,1052 190,1022 320,1028 C430,1034 480,1078 560,1112 C650,1146 800,1126 913,1112 L913,1191 Z" fill="#f4f3f1"/>
    </svg>

    <div class="food food-pizza" role="img" aria-label="Photo of a shrimp and tomato pizza"></div>
    <div class="food food-gumbo" role="img" aria-label="Photo of a bowl of chicken gumbo"></div>
    <div class="food food-poboy" role="img" aria-label="Photo of a shrimp po boy sandwich"></div>

    <div class="dish-label label-pizza">Pizza</div>
    <div class="dish-label label-gumbo">Chicken<br>Gumbo</div>
    <div class="dish-label label-poboy">Shrimp<br>Po Boy</div>

    <header class="brand-tab">
      <span class="brand-mark"></span>
      <div class="brand-name">Miss<br>Cobbler</div>
    </header>

    <section class="message">
      <h1 class="tagline">Homemade<br>Deliciousness</h1>
      <p class="pitch">
        <span class="xl">All of our</span>
        <span class="xl">vegetables</span>
        <span class="xl">are <span class="accent">Fresh</span></span>
        <span class="sm">and locally purchased</span>
        <span class="md">These recipes are</span>
        <span class="big">Originally</span>
        <span class="from">from</span>
        <span class="sm">New Orleans Louisiana</span>
      </p>
    </section>

    <div class="location-label">WHERE WE WILL BE !</div>
    <div class="location-box"></div>

    <div class="footer info">
      <div class="head">Information:</div>
      <div class="line">123-555-0190
        <span class="icon-box"><svg width="12" height="12" viewBox="0 0 24 24"><path d="M6.6 10.8a15 15 0 0 0 6.6 6.6l2.2-2.2a1 1 0 0 1 1-.25 11.4 11.4 0 0 0 3.6.6 1 1 0 0 1 1 1V20a1 1 0 0 1-1 1A17 17 0 0 1 3 4a1 1 0 0 1 1-1h3.5a1 1 0 0 1 1 1c0 1.25.2 2.45.6 3.6a1 1 0 0 1-.25 1z" fill="#fff"/></svg></span>
      </div>
      <div class="line">Misscobbler.net
        <span class="icon-box"><svg width="12" height="12" viewBox="0 0 24 24"><path d="M5 3l14 8-6 1.5L10 19z" fill="#fff"/></svg></span>
      </div>
    </div>
    <div class="divider"></div>
    <div class="footer social">
      <div class="head">Follow us :</div>
      <div class="squares"><span class="sq"></span><span class="sq"></span></div>
      <div class="line">misscobbler</div>
    </div>
  </div>
</div>
</body>
</html>
```